Toll Away Armed Harm

We need web design for an anti-gun violence campaign that will urge people to ring bells instead of shooting guns to bring in the New Year and whenever someone is killed by gun violence.
This campaign will raise funds for social agencies that help communities with social issues to help especially youth with no place to turn, play or dream. Also will fund New Gun Laws policies. Should be global in aspect but appealing to United States first.
Find poem by Lord Edmund Brackwell "Sing Larks, Swift Larks" as our theme on google.
This is a start up and nothing else to give. But need something eye catching for appeal of campaign.

Target Market(s)

Universal , more male oriented.

Industry/Entity Type

Gun

Number of Pages Required

1 page

Other font styles liked:
• Designers Can Choose

Requirements
Must have
• Strong imagery and vivid colors and bell of course.
Nice to have
• A stand out design beyond words that hit home. See attached file for website ideas

```html
<!DOCTYPE html>
<html lang="en">
<head>
<meta charset="utf-8">
<title>Toll Away Armed Harm</title>
<link rel="stylesheet" href="https://fonts.googleapis.com/css2?family=Open+Sans:ital,wght@0,400;0,600;1,400&display=swap">
<style>
:root{
  --brand-red:#e85a4c;
  --nav-gold:#f0b43a;
  --nav-active:#f4c83b;
  --nav-text:#6a4d1e;
  --accent-blue:#1b8fd2;
  --body-grey:#7a7a7a;
  --ink:#222;
  --rule:#dcdcdc;
  --panel:#f4f4f4;
  --footer-bg:#efefef;
  --footer-link:#555;
  --footer-head:#3ea2d4;
  --bottom-bar:#232323;
  --quote-gold:#f3c12e;
}
*{box-sizing:border-box;margin:0;padding:0}
html,body{width:862px;height:1200px;overflow:hidden;background:#fff}
body{font-family:"Open Sans",Arial,sans-serif;color:var(--ink);position:relative}
.site-header{position:absolute;top:0;left:0;width:862px;height:68px}
.site-title{position:absolute;left:71px;top:13px;font-size:30px;font-weight:400;color:var(--brand-red);letter-spacing:-0.2px}
.social-links{position:absolute;right:71px;top:22px;display:flex;gap:9px}
.social-links span{width:23px;height:23px;border-radius:50%;background:#bdbdbd;display:block}
.main-nav{position:absolute;top:68px;left:0;width:862px;height:32px;background:var(--nav-gold);border-top:1px solid #e6a52c}
.main-nav ul{list-style:none;display:flex;position:absolute;left:72px;top:0;height:31px}
.main-nav li{height:31px;line-height:31px;font-size:10.5px;color:var(--nav-text);padding:0 19px;border-right:1px solid #e2a233}
.main-nav li.active{background:var(--nav-active);padding:0 20px}
.hero{position:absolute;top:100px;left:0;width:862px;height:369px;background:linear-gradient(100deg,#2a2a2a 0%,#5a5a5a 30%,#8a8a8a 50%,#6a6a6a 70%,#9a9a9a 100%)}
.hero-arrow{position:absolute;top:172px;width:24px;height:24px;border-radius:50%;background:rgba(0,0,0,.55)}
.hero-arrow.prev{left:15px}.hero-arrow.next{right:15px}
.hero-arrow svg{display:block}
.hero-quote{position:absolute;left:71px;top:228px;width:274px;height:110px;background:rgba(0,0,0,.78);padding:10px 12px}
.hero-quote p{font-style:italic;color:#f2f2f2;font-size:15px;line-height:23.5px}
.hero-quote cite{display:block;text-align:right;font-style:normal;color:var(--quote-gold);font-size:11px;margin-top:6px}
.welcome{position:absolute;left:72px;top:500px;width:720px}
.welcome h1{font-size:16px;font-weight:400;color:var(--accent-blue);margin-bottom:7px}
.welcome p{font-size:9.6px;line-height:16.5px;color:var(--body-grey)}
.divider{position:absolute;left:72px;top:622px;width:720px;height:1px;background:var(--rule)}
.feature{position:absolute;top:650px;width:231px}
.feature h2{font-size:16px;font-weight:400;color:var(--accent-blue);margin:0 0 4px 1px;height:19px}
.feature .media{width:231px;height:122px;position:relative}
.feature p{font-size:9.6px;line-height:15.2px;color:var(--body-grey);margin-top:11px;padding-left:1px}
.feature p.dark{color:var(--ink)}
.f1{left:72px}.f2{left:317px}.f3{left:560px}
.media.gun{background:linear-gradient(90deg,#1c1c1c,#3a3a3a 60%,#777 85%,#aaa)}
.media.crowd{background:linear-gradient(180deg,#efe9dc 0%,#eee6d6 60%,#d46a3a 80%,#3a8ac0 100%)}
.media.hands{background:linear-gradient(180deg,#e8eef4 0%,#b88a6a 45%,#7a5a48 70%,#2a2a2a 100%)}
.progress{position:absolute;left:10px;right:12px;top:93px;height:7px;background:#f4cf2c}
.progress i{position:absolute;left:2px;top:2px;width:62%;height:3px;background:#8a1e14}
.progress-label{position:absolute;top:104px;font-size:7.5px;color:#fff}
.event-bar{position:absolute;left:71px;top:882px;width:720px;height:64px;background:var(--panel)}
.event-date{position:absolute;left:0;top:0;width:45px;height:64px;background:var(--accent-blue);color:#fff;text-align:center;padding-top:13px}
.event-date .month{font-size:12px;line-height:13px;font-weight:600}
.event-date .day{font-size:19px;line-height:22px;font-weight:600}
.event-body{position:absolute;left:67px;top:12px;width:580px}
.event-body h3{font-size:11px;font-weight:400;color:var(--ink)}
.event-body p{font-size:8.6px;line-height:12px;color:var(--body-grey);margin-top:4px}
.event-next{position:absolute;right:10px;top:21px}
.site-footer{position:absolute;left:0;top:973px;width:862px;height:183px;background:var(--footer-bg)}
.footer-col{position:absolute;top:23px}
.footer-col h4{font-size:11px;font-weight:400;color:var(--footer-head);margin-bottom:9px}
.footer-col ul{list-style:none}
.footer-col li{font-size:9px;line-height:18px;color:var(--footer-link)}
.c1{left:92px}.c2{left:234px}.c3{left:400px}.c4{left:556px}
.contact-form .field{width:166px;height:26px;background:#fff;border:1px solid #ddd;font-size:9px;color:#444;padding:7px 9px;margin-bottom:4px}
.contact-form .field.tall{height:48px}
.contact-form .submit{position:absolute;left:170px;top:138px;width:47px;height:23px;background:#555;color:#eee;font-size:9px;text-align:center;line-height:23px;border-radius:2px}
.bottom-bar{position:absolute;left:0;top:1156px;width:862px;height:44px;background:var(--bottom-bar);text-align:center;font-size:9px;line-height:44px;color:#aaa}
</style>
</head>
<body>
<header class="site-header">
  <div class="site-title">Toll Away Armed Harm</div>
  <div class="social-links" aria-label="Social links"><span></span><span></span><span></span><span></span></div>
</header>
<nav class="main-nav">
  <ul>
    <li class="active">HOME</li><li>ABOUT US</li><li>ABOUT GUN VIOLENCE</li><li>GET INVOLVED</li><li>DONATE NOW</li><li>EVENTS</li><li>CONTACT US</li>
  </ul>
</nav>
<section class="hero" role="img" aria-label="Black and white photograph of large church bells hanging against a stone wall">
  <div class="hero-arrow prev"><svg width="24" height="24"><path d="M14 6 L8 12 L14 18" stroke="#fff" stroke-width="3" fill="none"/></svg></div>
  <div class="hero-arrow next"><svg width="24" height="24"><path d="M10 6 L16 12 L10 18" stroke="#fff" stroke-width="3" fill="none"/></svg></div>
  <blockquote class="hero-quote">
    <p>Ring out, wild bells, to the wild sky,<br>The flying cloud, the frosty light<br>The year is dying in the night;</p>
    <cite>- Lord Edmund Brackwell</cite>
  </blockquote>
</section>
<section class="welcome">
  <h1>Welcome to Toll Away Armed Harm</h1>
  <p>In fermentum diam ac consequat scelerisque. Maecenas sagittis sem vitae arcu dictum tempus. Fusce sit amet ligula vel orci consectetur sodales laoreet vitae justo. Nam neque eros, auctor at auctor sed, placerat id odio. Praesent ornare ipsum turpis. Ut a cursus velit. Phasellus id viverra diam. Proin dignissim tempus facilisis. Aenean tellus enim, dapibus in enim non, ultrices rhoncus massa. Donec eu sollicitudin urna, vel congue elit. Sed a est efficitur, vestibulum orci sit amet, ullamcorper diam.</p>
</section>
<div class="divider"></div>
<article class="feature f1">
  <h2>About Gun Violence</h2>
  <div class="media gun" role="img" aria-label="Dark photo of a handgun tucked in a waistband"></div>
  <p>Aliquam et sem vitae libero egestas facilisis. Morbi tempus augue eu turpis elementum lacinia erat eu commodo porta, ipsum nibh dictum.</p>
</article>
<article class="feature f2">
  <h2>Get Involved</h2>
  <div class="media crowd" role="img" aria-label="Illustration of colourful crowd silhouettes raising their arms"></div>
  <p>Aliquam et sem vitae libero egestas facilisis. Morbi tempus augue eu turpis elementum lacinia erat eu commodo porta, ipsum nibh dictum.</p>
</article>
<article class="feature f3">
  <h2>Make a donation</h2>
  <div class="media hands" role="img" aria-label="Photo of many hands stacked together in unity">
    <div class="progress"><i></i></div>
    <span class="progress-label" style="left:12px">$0</span>
    <span class="progress-label" style="left:160px">$100000</span>
  </div>
  <p class="dark">All your funds goes to New Gun Laws policies Campaign</p>
</article>
<section class="event-bar">
  <div class="event-date"><div class="month">JUN</div><div class="day">22</div></div>
  <div class="event-body">
    <h3>Quisque libero orci, tincidunt ac massa vitae, gravida cursus urna</h3>
    <p>Aliquam vulputate orci at turpis volutpat pellentesque. Suspendisse viverra, dui ut consequat accumsan, odio purus aliquet sapien, vel dignissim odio leo nec tortor.</p>
  </div>
  <svg class="event-next" width="14" height="22"><path d="M2 1 L12 11 L2 21" stroke="#bbb" stroke-width="2" fill="none"/></svg>
</section>
<footer class="site-footer">
  <div class="footer-col c1"><h4>Navigation Menu</h4><ul><li>Home</li><li>About us</li><li>About Gun Violence</li><li>Get Involved</li><li>Donate Now</li><li>Events</li><li>Contact us</li></ul></div>
  <div class="footer-col c2"><h4>Support Links</h4><ul><li>Privacy Policy</li><li>Terms and Conditions</li><li>Customer Support</li><li>FAQ</li></ul></div>
  <div class="footer-col c3"><h4>Contact us</h4><ul><li>Call :&nbsp; 555 210 7730</li><li>Fax :&nbsp; 555 210 7731</li><li>E-mail: hello@tollaway.org</li></ul></div>
  <div class="footer-col c4 contact-form"><h4>Contact us</h4>
    <div class="field">Name</div><div class="field">E-mail</div><div class="field tall">Comment</div>
    <div class="submit">SUBMIT</div>
  </div>
</footer>
<div class="bottom-bar">Copyright &copy; 2014 Toll Away Armed Harm.&nbsp;&nbsp; All rights reserved.</div>
</body>
</html>
```